I need new business cards designed

I would like to get some new designs on business cards. I will upload my logo for reference. The business cards that were designed for me a few months ago were too difficult for the print companies to work with. My company is Quillbrook.net LLC. It is an art company that sells painting and expression cards online.

```html
<!DOCTYPE html>
<html lang="en">
<head>
<meta charset="utf-8">
<title>Quillbrook.net LLC – Business Card</title>
<link rel="stylesheet" href="https://fonts.googleapis.com/css2?family=Open+Sans:wght@400;600;700&display=swap">
<style>
  :root {
    --backdrop: #4a4a4a;
    --card: #161616;
    --edge: #0a9fdc;
    --brand-indigo: #3a3b8a;
    --accent-blue: #0aa0dc;
    --accent-orange: #f39221;
    --accent-clay: #d8845a;
    --ink-light: #f2f2f2;
  }
  * { box-sizing: border-box; margin: 0; padding: 0; }
  html, body {
    width: 1200px; height: 801px; overflow: hidden;
    background: var(--backdrop);
    font-family: "Open Sans", Arial, sans-serif;
  }
  .sheet {
    width: 1200px; height: 801px;
    display: flex; align-items: center; justify-content: center; gap: 40px;
  }
  .card {
    position: relative;
    width: 540px; height: 310px;
    background: var(--card);
    border-radius: 14px;
    border: 3px solid var(--edge);
    overflow: hidden;
  }

  /* Front */
  .brand-lockup { position: absolute; left: 32px; top: 128px; display: flex; align-items: center; gap: 12px; }
  .brand-square { width: 34px; height: 34px; background: var(--accent-orange); flex: none; }
  .brand-name { font-size: 25px; font-weight: 400; color: var(--brand-indigo); line-height: 1; }
  .tagline { font-size: 12px; line-height: 1.2; margin-top: 5px; color: var(--accent-blue); }

  .divider { position: absolute; left: 300px; top: 36px; width: 1.5px; height: 172px; background: var(--edge); }
  .contact { position: absolute; left: 318px; top: 34px; color: var(--ink-light); font-size: 13px; line-height: 1.55; }
  .contact .person { color: var(--accent-blue); font-size: 22px; font-weight: 700; letter-spacing: 0.5px; line-height: 1.1; }
  .contact .role { margin-bottom: 4px; }
  .contact .row { display: flex; align-items: center; gap: 7px; }
  .contact svg { width: 13px; height: 13px; flex: none; }

  .social { position: absolute; left: 34px; bottom: 26px; display: flex; gap: 10px; }
  .social span { width: 16px; height: 16px; border-radius: 50%; background: var(--accent-blue); }

  /* Back */
  .back-square { position: absolute; left: 42px; top: 74px; width: 150px; height: 150px; background: var(--accent-clay); }
  .back-lockup { position: absolute; left: 214px; top: 150px; }
  .back-lockup .brand-name { font-size: 44px; }
  .back-lockup .tagline { font-size: 19px; margin-top: 6px; }
</style>
</head>
<body>
<main class="sheet">

  <section class="card card-front" aria-label="Card front">
    <div class="brand-lockup">
      <div class="brand-square"></div>
      <div>
        <div class="brand-name">Quillbrook.net</div>
        <div class="tagline">Paintings and expression cards</div>
      </div>
    </div>

    <div class="divider"></div>

    <div class="contact">
      <div class="person">MARTIN HALE</div>
      <div class="role">Managing Director</div>
      <div>Your address, City</div>
      <div>State, Zip 1234</div>
      <div class="row">
        <svg viewBox="0 0 16 16" aria-hidden="true"><path fill="#0aa0dc" d="M3 1.5l3 .5 1 3.5-2 1.2a8 8 0 0 0 4.3 4.3l1.2-2 3.5 1 .5 3-1.5 1.5C7 14.5 1.5 9 1.5 3z"/></svg>
        <span>555-014-2687</span>
      </div>
      <div class="row">
        <svg viewBox="0 0 16 16" aria-hidden="true"><rect x="1" y="3" width="14" height="10" rx="1" fill="#0aa0dc"/><path d="M1.5 3.5L8 9l6.5-5.5" stroke="#161616" stroke-width="1.3" fill="none"/></svg>
        <span>hello@quillbrook.net</span>
      </div>
      <div class="row">
        <svg viewBox="0 0 16 16" aria-hidden="true"><circle cx="8" cy="8" r="6.5" fill="none" stroke="#0aa0dc" stroke-width="1.5"/><path d="M1.5 8h13M8 1.5c-3 3.5-3 9.5 0 13M8 1.5c3 3.5 3 9.5 0 13" stroke="#0aa0dc" stroke-width="1.2" fill="none"/></svg>
        <span>www.Quillbrook.net</span>
      </div>
    </div>

    <div class="social" aria-hidden="true"><span></span><span></span><span></span></div>
  </section>

  <section class="card card-back" aria-label="Card back">
    <div class="back-square"></div>
    <div class="back-lockup">
      <div class="brand-name">Quillbrook.net</div>
      <div class="tagline">Paintings and expression cards</div>
    </div>
  </section>

</main>
</body>
</html>
```